packaging design for disposable trash bag

We need 3 design for 3 of our products. first item is trash bag,the second item is disposable table cover and third is food packaging bag . We are a company in Singapore selling disposable product. This packaging products will be sold on shelf or online.

Attached is the requirement of the product. And some samples.

Target Market(s)

adult, most likely housewife

Requirements
Must have
• Packing design requirement for trash bag
• 1. Include company logo design, which is attached in the creative brief. DARVELLO POLYMER.
• 2. Clear showing of the product and its illustration of using. Eg. The trash bin.
• 3. Allocate a box for the purpose of sticking product size sticker.
• 4. Each packing bag holds 10pcs
• 5. Show of country of origin. Product of Singapore.
• 6. Use of one colour for printing of packing bag ( Black / blue/ bright Green/ white )
• 7. Show of warning: Keep polythene bags away from young children
• 8. dimension of the packagaing printing area : Lenght : 20 cm , Height 26 cm
• Packing design requirement for disposable Table Cover
• 1. Include company logo design, which is attached in the creative brief. Our company is DARVELLO POLYMER.
• 2. Clear showing of the product and its illustration of using. Eg. The table?.
• 4. Each packing bag holds 5pcs
• 6. Use of one colour for printing of the packing bag ( Black / blue/ bright Green )
• Packing design requirement for disposable food packaging plastic bag
• 2. Clear showing of the product and its illustration of using. Eg. Food?.
• 4. Show of country of origin. Product of Singapore.
• 5. Use of one colour for printing of the packing bag ( Black/ bright green )
• 6. Show of warning: Keep polythene bags away from young children
• 7. Show of product information: hygienic, food grade, freezer resistance, grease proof, damp proof, heat resistant.
• 8. Include the open here packing opening.
• 9. dimension of the packagaing printing area : Lenght : 15 cm , Height 22 cm
Nice to have
• requirement is stated in the must have. Good to allocate some space beside the packaging PCS area for promotion stickers . And also space allocated for bar code stickers.
Should not have
• no more than one color for printing

```html
<!DOCTYPE html>
<html lang="en">
<head>
<meta charset="utf-8">
<title>Darvello Polymer – Disposable Food Packaging Plastic Bag</title>
<link href="https://fonts.googleapis.com/css2?family=Anton&family=Archivo+Black&family=Oswald:wght@500;700&family=Roboto:wght@400;700&display=swap" rel="stylesheet">
<style>
  :root {
    --ink: #111111;
    --film: #d6dbe7;
    --page: #ffffff;
    --placeholder: #9aa0ab;
  }
  html, body {
    margin: 0;
    padding: 0;
    width: 1200px;
    height: 766px;
    overflow: hidden;
    background: var(--page);
  }
  .pack { display: block; width: 1200px; height: 766px; }
  .pack-face { fill: var(--film); }
  .rule { stroke: var(--ink); fill: none; }
  .ink { fill: var(--ink); }
  .size-tag { font-family: "Archivo Black", sans-serif; font-size: 17px; letter-spacing: 1px; }
  .title-small { font-family: "Archivo Black", sans-serif; font-size: 44px; }
  .title-main { font-family: "Anton", sans-serif; font-size: 120px; }
  .disposal-note { font-family: "Oswald", sans-serif; font-weight: 500; font-size: 16px; }
  .feature { font-family: "Archivo Black", sans-serif; font-size: 25px; }
  .label { font-family: "Roboto", sans-serif; font-weight: 700; font-size: 19px; }
  .label-small { font-family: "Roboto", sans-serif; font-weight: 700; font-size: 14px; letter-spacing: 0.5px; }
  .brand-name { font-family: "Roboto", sans-serif; font-weight: 400; font-size: 33px; }
  .brand-url { font-family: "Roboto", sans-serif; font-weight: 700; font-size: 25px; }
  .eco-title { font-family: "Oswald", sans-serif; font-weight: 700; font-size: 32px; }
  .origin { font-family: "Roboto", sans-serif; font-weight: 400; font-size: 22px; }
  .warning { font-family: "Archivo Black", sans-serif; font-size: 19px; }
  .warning-body { font-family: "Roboto", sans-serif; font-weight: 700; font-size: 19px; }
  .placeholder { fill: var(--placeholder); }
</style>
</head>
<body>
<svg class="pack" viewBox="0 0 1500 958" xmlns="http://www.w3.org/2000/svg">
  <rect class="pack-face" x="60" y="62" width="1380" height="834" rx="40"/>

  <rect class="rule" x="198" y="100" width="1100" height="748" rx="20" stroke-width="5"/>

  <g class="size-box">
    <line class="rule" x1="330" y1="124" x2="347" y2="124" stroke-width="6"/>
    <text class="size-tag ink" x="386" y="131" text-anchor="middle">SIZE</text>
    <line class="rule" x1="425" y1="124" x2="1290" y2="124" stroke-width="6"/>
    <polyline class="rule" points="203,124 203,322 572,322 572,124" stroke-width="5"/>
    <path class="rule" stroke-width="4" d="M210 172 V147 H243 M530 147 H563 V172 M210 278 V303 H243 M530 303 H563 V278"/>
    <text class="label ink" x="386" y="230" text-anchor="middle">SIZE (DIMENSION)</text>
  </g>

  <g class="title-block">
    <line class="rule" x1="580" y1="130" x2="580" y2="322" stroke-width="5"/>
    <line class="rule" x1="1022" y1="322" x2="1290" y2="322" stroke-width="5"/>
    <text class="title-small ink" x="1252" y="182" text-anchor="end">DISPOSABLE</text>
    <text class="title-main ink" x="615" y="285" textLength="637" lengthAdjust="spacingAndGlyphs">FOOD PACKAGING PLASTIC BAG</text>
    <text class="disposal-note ink" x="598" y="313" textLength="677" lengthAdjust="spacingAndGlyphs">USED BAGS SHOULD BE DISPOSED OF IN A PROPER MANNER TO ENSURE CLEANLINESS TO THE SURROUNDING ENVIRONMENT.</text>
  </g>

  <g class="features">
    <path class="ink" d="M223 349 L233 359 L223 369 Z M223 387 L233 397 L223 407 Z M223 425 L233 435 L223 445 Z M223 463 L233 473 L223 483 Z M223 501 L233 511 L223 521 Z M223 539 L233 549 L223 559 Z"/>
    <text class="feature ink" x="240" y="368" textLength="111" lengthAdjust="spacingAndGlyphs">HYGENIC</text>
    <text class="feature ink" x="240" y="406" textLength="162" lengthAdjust="spacingAndGlyphs">FOOD GRADE</text>
    <text class="feature ink" x="240" y="444" textLength="194" lengthAdjust="spacingAndGlyphs">GREASE PROOF</text>
    <text class="feature ink" x="240" y="482" textLength="170" lengthAdjust="spacingAndGlyphs">DAMP PROOF</text>
    <text class="feature ink" x="240" y="520" textLength="257" lengthAdjust="spacingAndGlyphs">FREEZER RESISTANT</text>
    <text class="feature ink" x="240" y="558" textLength="210" lengthAdjust="spacingAndGlyphs">HEAT RESISTANT</text>
  </g>

  <g class="open-here">
    <ellipse class="rule" cx="748" cy="467" rx="240" ry="118" stroke-width="5"/>
    <ellipse class="rule" cx="748" cy="467" rx="228" ry="106" stroke-width="2" stroke-dasharray="6 4"/>
    <polyline class="rule" points="640,447 616,470 640,493" stroke-width="6"/>
    <polyline class="rule" points="856,447 880,470 856,493" stroke-width="6"/>
    <text class="label ink" x="747" y="474" text-anchor="middle" font-size="18">OPEN HERE</text>
  </g>

  <rect class="placeholder" x="1025" y="382" width="255" height="98" rx="10" role="img" aria-label="Pictograms of a drink, a bowl of soup and a plate of noodles"/>
  <text class="label-small ink" x="1142" y="507" text-anchor="middle">SUITABLE FOR</text>
  <text class="label-small ink" x="1142" y="526" text-anchor="middle">MOST FOOD PACKAGING</text>

  <line class="rule" x1="200" y1="580" x2="582" y2="580" stroke-width="6"/>
  <line class="rule" x1="913" y1="580" x2="1296" y2="580" stroke-width="6"/>

  <g class="brand">
    <rect class="ink" x="372" y="620" width="48" height="48"/>
    <text class="brand-name ink" x="396" y="729" text-anchor="middle">DARVELLO POLYMER</text>
    <text class="brand-name ink" x="396" y="762" text-anchor="middle">PTE LTD</text>
    <text class="brand-url ink" x="396" y="788" text-anchor="middle">www.darvellopolymer.com</text>
  </g>

  <g class="eco">
    <text class="eco-title ink" x="673" y="650" textLength="150" lengthAdjust="spacingAndGlyphs">OXO-BIODEGRADABLE</text>
    <rect class="placeholder" x="688" y="662" width="118" height="80" rx="8" role="img" aria-label="Leaf illustration with go green wording"/>
    <polygon class="ink" points="680,752 658,792 702,792"/>
    <rect class="ink" x="712" y="756" width="34" height="36"/>
    <circle class="ink" cx="777" cy="775" r="19"/>
    <rect class="ink" x="808" y="756" width="30" height="36"/>
  </g>

  <g class="origin-box">
    <text class="origin ink" x="983" y="620" textLength="234" lengthAdjust="spacingAndGlyphs">PRODUCT OF SINGAPORE</text>
    <path class="rule" stroke-width="4" d="M947 664 V632 H980 M1220 632 H1253 V664 M947 754 V786 H980 M1220 786 H1253 V754"/>
    <text class="label ink" x="1100" y="716" text-anchor="middle">BARCODE</text>
  </g>

  <line class="rule" x1="200" y1="817" x2="1296" y2="817" stroke-width="5"/>
  <text class="warning ink" x="234" y="840" textLength="182" lengthAdjust="spacingAndGlyphs">WARNING:</text>
  <text class="warning-body ink" x="428" y="840" textLength="832" lengthAdjust="spacingAndGlyphs">PLEASE KEEP POLYTHENE BAGS AWAY FROM YOUNG CHILDREN</text>
</svg>
</body>
</html>
```